The Brookhaven Sessions - Concert Series Website Design

I've recently decided to launch a concert series in my living room and would love a website to use to promote the series. I'm looking for a simple Wix design that I could take over once it's complete. I'll provide the logo for which I'd like the website to utilize the color scheme.

Target Market(s)

Music lovers in Denver

Industry/Entity Type

Music

Coding

Coded - Design and coding required

Number of Pages Required

2 page

Font styles to use
Script

Requirements
Must have
• 2 pages - one for concert goers to see the schedule and rsvp, and one for artists about the booking process

```html
<!DOCTYPE html>
<html lang="en">
<head>
<meta charset="utf-8">
<title>The Brookhaven Sessions</title>
<link href="https://fonts.googleapis.com/css2?family=Cinzel:wght@400;600&family=Lato:ital,wght@0,400;0,700;0,900;1,400&display=swap" rel="stylesheet">
<style>
:root{
  --plum:#4a1448;
  --plum-dark:#3a0f3b;
  --orange:#f7a94c;
  --ink:#1d1020;
  --text:#5a4b5a;
  --white:#ffffff;
}
*{box-sizing:border-box;margin:0;padding:0}
html,body{width:1200px;height:3039px;overflow:hidden}
body{position:relative;font-family:"Lato",sans-serif;background:var(--white);color:var(--ink)}
.abs{position:absolute}
.btn{position:absolute;display:flex;align-items:center;justify-content:center;border-radius:24px;font-weight:900;font-size:14px;color:var(--white);text-transform:uppercase;letter-spacing:-.2px}
.btn-plum{background:var(--plum)}
.btn-orange{background:var(--orange)}

/* hero */
.hero{left:0;top:0;width:1200px;height:800px;background:radial-gradient(ellipse at 75% 30%,#e3892c 0%,#a3452a 25%,#3a1d5a 55%,#141a5c 80%,#0c0f3a 100%)}
.brand{left:110px;top:28px;display:flex;align-items:center;gap:14px;color:var(--white)}
.brand-mark{width:82px;height:86px;border-radius:50%;background:var(--orange);border:4px solid #c0413f}
.brand-name{font-family:"Lato",sans-serif;font-size:28px;line-height:28px;text-transform:uppercase;letter-spacing:-.5px}
.nav{top:36px;font-size:17px;color:var(--white)}
.nav-home{left:598px;font-weight:700}
.nav-home:after{content:"";position:absolute;left:0;right:0;top:26px;height:3px;background:var(--white)}
.nav-about{left:686px}
.headline{left:110px;top:222px;font-family:"Cinzel",serif;font-weight:400;font-size:70px;line-height:84px;color:var(--white);letter-spacing:2px;text-transform:uppercase}
.headline span{color:var(--orange)}
.tagline{left:110px;top:488px;font-size:22px;color:var(--white);letter-spacing:.6px}
.wave{left:0;top:640px}

/* shows */
.section-title{left:0;width:1200px;text-align:center;font-family:"Cinzel",serif;font-weight:400;font-size:44px;letter-spacing:2px;color:var(--ink);text-transform:uppercase}
.section-title b{color:var(--plum);font-weight:600}
.section-sub{left:0;width:1200px;text-align:center;font-style:italic;font-size:19px;color:var(--orange)}
.card-photo{top:980px;width:235px;height:284px;border-radius:6px}
.date-badge{position:absolute;right:0;top:0;width:86px;height:86px;background:var(--orange);border:3px solid var(--white);border-top:none;border-right:none;border-radius:0 6px 0 10px;color:var(--white);font-size:15px;line-height:26px;text-align:center;padding-top:18px}
.artist{top:1284px;font-size:23px;color:var(--ink);font-weight:400}
.genre{top:1322px;font-size:15px;color:var(--plum)}

/* reserve */
.reserve{left:0;top:1508px;width:1200px;height:600px;background:radial-gradient(ellipse at 50% 85%,#e0456a 0%,#a5234f 35%,#661240 65%,#2a0a24 100%)}
.reserve-title{left:0;top:1570px;width:1200px;text-align:center;font-family:"Cinzel",serif;font-weight:400;font-size:44px;color:var(--white);letter-spacing:2px;text-transform:uppercase}
.reserve-title b{font-weight:600}
.reserve-copy{left:0;top:1648px;width:1200px;text-align:center;font-size:16px;line-height:27px;color:var(--white)}
.field{position:absolute;height:48px;width:419px;background:var(--white);border-radius:24px;font-size:15px;color:#666;display:flex;align-items:center;padding-left:28px;justify-content:space-between;padding-right:22px}
.chev{width:12px;height:12px;border-right:2px solid #888;border-bottom:2px solid #888;transform:rotate(45deg) translateY(-4px)}
.consent{left:283px;top:1933px;display:flex;align-items:center;gap:14px;font-style:italic;font-size:13px;color:var(--white)}
.box{width:14px;height:14px;border:2px solid var(--white)}

/* about */
.about-title{left:110px;top:2186px;font-family:"Cinzel",serif;font-weight:400;font-size:44px;letter-spacing:2px;text-transform:uppercase}
.about-title b{color:var(--plum);font-weight:600}
.about-sub{left:110px;top:2248px;font-size:22px;color:var(--orange)}
.about-copy{left:110px;width:430px;font-size:14.5px;line-height:27.5px;color:var(--text)}
.about-photo{left:665px;top:2195px;width:394px;height:394px;border-radius:50%;background:radial-gradient(circle at 50% 45%,#b4553c 0%,#6b2e2a 50%,#2e1a22 100%)}

/* footer */
.footer-wave{left:0;top:2595px}
.footer{left:0;top:2740px;width:1200px;height:299px;background:var(--plum-dark)}
.footer-logo{left:125px;top:2768px;width:190px;height:218px;border-radius:16px 16px 95px 95px;background:linear-gradient(#f6a54b,#c0413f);display:flex;align-items:flex-end;justify-content:center;padding-bottom:48px;color:var(--white);font-family:"Lato",sans-serif;font-size:18px;text-align:center;line-height:20px;text-transform:uppercase}
.contact{display:flex;align-items:center;gap:16px;color:var(--white);font-size:21px}
.icon{width:40px;height:40px;border-radius:50%;background:var(--white);display:flex;align-items:center;justify-content:center}
.social{top:2936px;width:30px;height:30px;border-radius:50%;background:var(--white)}
.rule{left:110px;top:3010px;width:980px;height:1px;background:#c9b8c9}
.copyright{left:0;top:3018px;width:1200px;text-align:center;font-size:12px;color:var(--white)}
</style>
</head>
<body>

<section class="hero abs" role="img" aria-label="Live band performing on a warmly lit stage"></section>
<div class="brand abs">
  <div class="brand-mark"></div>
  <div class="brand-name">The Brookhaven<br>Sessions</div>
</div>
<div class="nav nav-home abs">Home</div>
<div class="nav nav-about abs">About The Series</div>
<div class="btn btn-plum" style="left:875px;top:32px;width:222px;height:42px">RSVP to the next session</div>
<h1 class="headline abs">Where <span>Music</span><br><span>Meets</span> Golden<br>Hour</h1>
<p class="tagline abs">An intimate living-room concert series in Denver.</p>
<div class="btn btn-plum" style="left:112px;top:548px;width:170px;height:42px">Reserve your seat</div>
<div class="btn btn-orange" style="left:292px;top:548px;width:205px;height:42px">Join the next session</div>
<svg class="wave abs" width="1200" height="170" viewBox="0 0 1200 170">
  <path d="M0 100 C200 50 420 40 600 90 C780 140 1000 140 1200 90 L1200 170 L0 170Z" fill="#fff"/>
  <path d="M0 100 C200 50 420 40 600 90 C780 140 1000 140 1200 90" fill="none" stroke="#f7a94c" stroke-width="8"/>
</svg>

<h2 class="section-title abs" style="top:858px">Upcoming <b>Shows</b></h2>
<p class="section-sub abs" style="top:922px">An Intimate Evening of Live Music</p>

<div class="card-photo abs" style="left:110px;background:linear-gradient(160deg,#5a1f5e,#c2456b,#2a1030)" role="img" aria-label="Singer-songwriter at a keyboard"><div class="date-badge">March 24<br>7:30 PM</div></div>
<div class="card-photo abs" style="left:357px;background:linear-gradient(160deg,#2a1a12,#8a4a1e,#1a0f0a)" role="img" aria-label="Violinist performing"><div class="date-badge">April 7<br>7:30 PM</div></div>
<div class="card-photo abs" style="left:605px;background:linear-gradient(160deg,#e6e4e2,#9a8f88,#3b4a8a)" role="img" aria-label="Musician playing keyboard with headphones"><div class="date-badge">April 21<br>7:30 PM</div></div>
<div class="card-photo abs" style="left:852px;background:linear-gradient(160deg,#1e3a4e,#6a7a86,#2a3440)" role="img" aria-label="Violinist in a light dress"><div class="date-badge">May 5<br>7:30 PM</div></div>

<h3 class="artist abs" style="left:113px">Nora Vale</h3>
<h3 class="artist abs" style="left:360px">Hollis &amp; The Pines</h3>
<h3 class="artist abs" style="left:608px">Theo Marsh</h3>
<h3 class="artist abs" style="left:855px">Lena Ortiz</h3>
<p class="genre abs" style="left:113px">Indie Folk / Singer-Songwriter</p>
<p class="genre abs" style="left:360px">Americana / Acoustic Duo</p>
<p class="genre abs" style="left:608px">Indie / Alternative Acoustic</p>
<p class="genre abs" style="left:855px">Indie Pop / Soul</p>
<div class="btn btn-plum" style="left:110px;top:1366px;width:170px;height:42px">Reserve your seat</div>
<div class="btn btn-plum" style="left:357px;top:1366px;width:170px;height:42px">Reserve your seat</div>
<div class="btn btn-plum" style="left:605px;top:1366px;width:170px;height:42px">Reserve your seat</div>
<div class="btn btn-plum" style="left:852px;top:1366px;width:170px;height:42px">Reserve your seat</div>

<section class="reserve abs" role="img" aria-label="Empty concert stage lit in pink and red"></section>
<h2 class="reserve-title abs">Reserve <b>Your Seat</b></h2>
<p class="reserve-copy abs">Each session is intentionally limited to preserve the experience.<br>Complete the form below to request your seat. Event details and confirmation will be sent via email.</p>
<div class="field" style="left:171px;top:1735px">Full Name</div>
<div class="field" style="left:602px;top:1735px">Email Address</div>
<div class="field" style="left:171px;top:1793px">Phone Number</div>
<div class="field" style="left:602px;top:1793px">Select the Show You'd Like to Attend<span class="chev"></span></div>
<div class="field" style="left:171px;top:1854px">Number of Seats Requested<span class="chev"></span></div>
<div class="field" style="left:602px;top:1854px">How did you hear about The Brookhaven Sessions?</div>
<div class="consent abs"><span class="box"></span>I understand seating is limited and my reservation is not confirmed until I receive a confirmation email.</div>
<div class="btn btn-orange" style="left:515px;top:1979px;width:170px;height:42px">Reserve my seat</div>

<h2 class="about-title abs">About <b>The Series</b></h2>
<p class="about-sub abs">An Elevated Listening Experience</p>
<p class="about-copy abs" style="top:2294px">The Brookhaven Sessions is an intimate concert series hosted in a Denver living room, created for music lovers who value connection, presence, and sound in its most human form.</p>
<p class="about-copy abs" style="top:2389px">Each session is carefully curated — from the artists we invite to the atmosphere we create. Seating is intentionally limited, distractions are left at the door, and the focus remains where it belongs: on the music and the shared experience of being in the room.</p>
<div class="btn btn-plum" style="left:110px;top:2531px;width:120px;height:42px">Read more</div>
<div class="about-photo abs" role="img" aria-label="Acoustic band playing in a cosy living room"></div>

<svg class="footer-wave abs" width="1200" height="150" viewBox="0 0 1200 150">
  <path d="M0 100 C200 50 420 40 600 90 C780 140 1000 140 1200 90 L1200 150 L0 150Z" fill="#3a0f3b"/>
  <path d="M0 100 C200 50 420 40 600 90 C780 140 1000 140 1200 90" fill="none" stroke="#f7a94c" stroke-width="8"/>
</svg>
<footer class="footer abs"></footer>
<div class="footer-logo abs">The Brookhaven<br>Sessions</div>
<div class="contact abs" style="left:392px;top:2827px">
  <span class="icon"><svg width="20" height="20" viewBox="0 0 24 24"><path d="M6.6 10.8a15 15 0 006.6 6.6l2.2-2.2c.3-.3.7-.4 1-.2 1.1.4 2.3.6 3.6.6.6 0 1 .4 1 1V20c0 .6-.4 1-1 1A17 17 0 013 4c0-.6.4-1 1-1h3.5c.6 0 1 .4 1 1 0 1.3.2 2.5.6 3.6.1.3 0 .7-.2 1z" fill="#3a0f3b"/></svg></span>+1 555 014 2290</div>
<div class="contact abs" style="left:712px;top:2827px">
  <span class="icon"><svg width="22" height="22" viewBox="0 0 24 24"><rect x="3" y="6" width="18" height="12" rx="2" fill="none" stroke="#3a0f3b" stroke-width="2"/><path d="M3 7l9 6 9-6" fill="none" stroke="#3a0f3b" stroke-width="2"/></svg></span>info@thebrookhavensessions.com</div>
<div class="contact abs" style="left:392px;top:2911px">
  <span class="icon"><svg width="20" height="20" viewBox="0 0 24 24"><path d="M12 2a7 7 0 00-7 7c0 5 7 13 7 13s7-8 7-13a7 7 0 00-7-7zm0 9.5a2.5 2.5 0 110-5 2.5 2.5 0 010 5z" fill="#3a0f3b"/></svg></span>12 Aspen Row, Denver 80205</div>
<div class="social abs" style="left:941px;background:var(--orange)" aria-label="Social profile"></div>
<div class="social abs" style="left:976px" aria-label="Social profile"></div>
<div class="social abs" style="left:1014px" aria-label="Social profile"></div>
<div class="social abs" style="left:1052px" aria-label="Social profile"></div>
<div class="rule abs"></div>
<p class="copyright abs">Copyright © 2026 The Brookhaven Sessions. All rights reserved.</p>

</body>
</html>
```